QVR business card

Need a business card for a company that provides instructional design and elearning development services. The website is here: http://quorvane.studio/

I'm attaching a current logo, as well as the old business card design. While I like to keep it clean, the old design is too simplistic for my liking. The only idea I want to reuse from the old design is placing industry jargon on the back of the card, just need a better way to present it. But if you have other ideas for the back--feel free to experiment.

Please use the colors complementary to the color we have on the website. Thank you!

```html
<!DOCTYPE html>
<html lang="en">
<head>
<meta charset="utf-8">
<title>QVR Business Card</title>
<link href="https://fonts.googleapis.com/css2?family=Open+Sans:wght@400;600;700&display=swap" rel="stylesheet">
<style>
  :root {
    --teal: #1bb3b0;
    --teal-deep: #17a6a8;
    --sand: #d9c98f;
    --sand-soft: #ded29f;
    --ink: #2b2b2b;
    --paper: #ffffff;
    --mist: #dfe3e4;
    --stage: #ecebe8;
  }
  * { box-sizing: border-box; margin: 0; padding: 0; }
  html, body { width: 1200px; height: 675px; overflow: hidden; }
  body {
    background: var(--stage);
    font-family: "Open Sans", Arial, sans-serif;
    position: relative;
  }
  .card {
    position: absolute;
    top: 188px;
    width: 520px;
    height: 300px;
    overflow: hidden;
    box-shadow: 0 6px 18px rgba(0,0,0,0.18);
  }
  /* Front side */
  .card-front {
    left: 50px;
    background: linear-gradient(180deg, var(--teal) 0%, #7ebfae 50%, var(--sand) 88%);
  }
  .world-map {
    position: absolute;
    left: 120px; top: 14px;
    width: 340px; height: 170px;
    background: radial-gradient(ellipse at center, rgba(255,255,255,0.14), rgba(255,255,255,0) 70%);
    border-radius: 40%;
  }
  .url-pill {
    position: absolute;
    right: 0; top: 92px;
    width: 250px; height: 30px;
    background: var(--sand-soft);
    border-radius: 15px 0 0 15px;
    color: var(--paper);
    font-size: 14px;
    letter-spacing: 2px;
    line-height: 30px;
    padding-left: 20px;
  }
  .brand-front {
    position: absolute;
    left: 36px; top: 128px;
    display: flex; align-items: center; gap: 10px;
    color: var(--paper);
    font-weight: 700;
    font-size: 34px;
    letter-spacing: 1px;
  }
  .brand-front .mark { width: 16px; height: 16px; background: var(--paper); border-radius: 50%; }
  .services {
    position: absolute;
    right: 28px; bottom: 28px;
    list-style: none;
    text-align: right;
    color: var(--ink);
    font-size: 14px;
    line-height: 20px;
  }
  .services li { display: flex; justify-content: flex-end; align-items: center; gap: 10px; }
  .services svg { width: 14px; height: 14px; }
  /* Back side */
  .card-back {
    left: 630px;
    background: var(--paper);
  }
  .tab {
    position: absolute;
    left: 0; top: 40px;
    width: 28px; height: 28px;
    background: var(--sand-soft);
    border-radius: 0 14px 14px 0;
  }
  .person { position: absolute; left: 40px; top: 38px; }
  .person-name {
    color: var(--teal-deep);
    font-weight: 700;
    font-size: 18px;
    letter-spacing: 0.5px;
  }
  .person-role { color: var(--ink); font-size: 13px; }
  .contacts {
    position: absolute;
    left: 40px; top: 150px;
    list-style: none;
    font-size: 14px;
    color: var(--ink);
    line-height: 22px;
  }
  .contacts li { display: flex; align-items: center; gap: 10px; }
  .contacts svg { width: 14px; height: 14px; }
  .faint-mark {
    position: absolute;
    right: -40px; top: 70px;
    width: 200px; height: 200px;
    background: var(--mist);
    border-radius: 50%;
    opacity: 0.7;
  }
  .brand-back {
    position: absolute;
    right: 40px; bottom: 34px;
    display: flex; align-items: center; gap: 10px;
    color: var(--sand);
    font-weight: 700;
    font-size: 34px;
    letter-spacing: 1px;
  }
  .brand-back .mark { width: 16px; height: 16px; background: var(--teal); border-radius: 50%; }
</style>
</head>
<body>
  <section class="card card-front">
    <div class="world-map" role="img" aria-label="Dotted world map pattern"></div>
    <div class="url-pill">www.quorvane.studio</div>
    <div class="brand-front"><span class="mark"></span><span>QVR</span></div>
    <ul class="services">
      <li>Instructional Design
        <svg viewBox="0 0 14 14"><rect x="1" y="1" width="12" height="12" rx="2" fill="#fff"/></svg></li>
      <li>Elearning Development
        <svg viewBox="0 0 14 14"><rect x="1" y="3" width="12" height="8" rx="1" fill="none" stroke="#fff" stroke-width="2"/></svg></li>
      <li>Mobile Learning
        <svg viewBox="0 0 14 14"><rect x="3" y="1" width="8" height="12" rx="1.5" fill="none" stroke="#fff" stroke-width="2"/></svg></li>
      <li>Instructor-LED Training
        <svg viewBox="0 0 14 14"><circle cx="7" cy="7" r="5" fill="none" stroke="#fff" stroke-width="2"/></svg></li>
    </ul>
  </section>

  <section class="card card-back">
    <div class="tab"></div>
    <div class="person">
      <div class="person-name">MARIN KESSLER</div>
      <div class="person-role">Managing Director</div>
    </div>
    <ul class="contacts">
      <li><svg viewBox="0 0 14 14"><path d="M3 1h3l1 3-2 1.5a8 8 0 0 0 3.5 3.5L10 7l3 1v3a2 2 0 0 1-2 2A10 10 0 0 1 1 3a2 2 0 0 1 2-2z" fill="var(--teal-deep)"/></svg>555-014-2873</li>
      <li><svg viewBox="0 0 14 14"><rect x="1" y="3" width="12" height="8" rx="1" fill="var(--teal-deep)"/><path d="M1.5 3.5 7 8l5.5-4.5" fill="none" stroke="#fff" stroke-width="1.2"/></svg>mkessler@quorvane.studio</li>
      <li><svg viewBox="0 0 14 14"><circle cx="7" cy="7" r="6" fill="none" stroke="var(--teal-deep)" stroke-width="1.5"/><path d="M1 7h12M7 1c-3 3-3 9 0 12M7 1c3 3 3 9 0 12" fill="none" stroke="var(--teal-deep)" stroke-width="1.2"/></svg>www.quorvane.studio</li>
    </ul>
    <div class="faint-mark"></div>
    <div class="brand-back"><span class="mark"></span><span>QVR</span></div>
  </section>
</body>
</html>
```